BRISK requires an exciting new business card

New business card required for BRISK. We are a new market research consultancy and want our brand to be approachable and be contemporary/modern, bold, uncomplicated/simple, and use friendly and easy to read fonts.

A draft website front page is attached to give you a feel (the pictures will be improved over the coming days).

The business card will be printed on 600gsm card, full colour both sides. The card is unique in that it allows one of four colours to be placed within the seam of the card (see http://uk.prentvo.com/products/gilt/business-cards.html)

The logo has been designed in yellow on white, white on yellow, yellow on black and black on yellow - please select whichever you feel most appropriate from the attached document (please use the versions with the tagline). I think my preference is yellow on white for the front, and then yellow or black as the dominant colour on the back.

Telephone numbers will be given next week as they are now being finalised.

Thanks

Target Market(s)

Professionals in large corporates, such as Marketing Managers at Grovane, Fizzaro Pop, Delmarco etc.

Industry/Entity Type

Market Research

Requirements
Must have
• Dana Pruitt MRPC
brisk
Level 4, 37 Quarrell St
Surrey Hills
NSW 2010
Tel: 02 XXXX XXXX
Mob: XXXX XXXXXX
Email: dana@briskqr.com.au
Web: www.briskqr.com.au

```html
<!DOCTYPE html>
<html lang="en">
<head>
<meta charset="utf-8">
<title>BRISK business card</title>
<link href="https://fonts.googleapis.com/css2?family=Open+Sans:wght@400;600;700&display=swap" rel="stylesheet">
<style>
  :root {
    --yellow: #ffc800;
    --charcoal: #3d3d3f;
    --ink: #333335;
    --grey-line: #d6d6d8;
    --card: #ffffff;
    --backdrop: #e8e8ee;
  }
  * { box-sizing: border-box; margin: 0; padding: 0; }
  html, body {
    width: 1200px; height: 987px; overflow: hidden;
    background: var(--backdrop);
    font-family: "Open Sans", Arial, sans-serif;
  }
  .sheet {
    width: 1200px; height: 987px;
    display: flex; flex-direction: column; align-items: center; justify-content: center; gap: 56px;
  }
  .card {
    position: relative; width: 700px; height: 427px;
    background: var(--card); border-radius: 30px; overflow: hidden;
    box-shadow: 0 6px 18px rgba(0,0,0,0.12);
  }
  .card__swoosh { position: absolute; inset: 0; width: 100%; height: 100%; }

  .brand { position: absolute; color: var(--yellow); }
  .brand__name { font-weight: 700; line-height: 1; letter-spacing: -2px; display: flex; align-items: center; }
  .brand__dot { display: inline-block; border-radius: 50%; background: var(--yellow); }
  .brand__tagline { color: var(--ink); font-weight: 400; }

  .card--details .brand { left: 46px; top: 34px; }
  .card--details .brand__name { font-size: 104px; }
  .card--details .brand__dot { width: 34px; height: 34px; margin-left: 14px; margin-top: 28px; }
  .card--details .brand__tagline { font-size: 21px; margin-top: -2px; margin-left: 4px; }

  .divider { position: absolute; left: 372px; top: 60px; width: 2px; height: 210px; background: var(--grey-line); }

  .contact { position: absolute; left: 396px; top: 66px; color: var(--ink); font-size: 18px; line-height: 1.42; }
  .contact__name { color: var(--yellow); font-weight: 700; font-size: 21px; margin-bottom: 8px; }
  .contact__name span { font-weight: 400; }
  .contact__address { margin-bottom: 10px; }
  .contact__row { display: flex; align-items: center; gap: 8px; }
  .contact__icon { width: 16px; height: 16px; flex: none; }

  .card--logo .brand { left: 0; right: 0; top: 88px; text-align: center; }
  .card--logo .brand__name { justify-content: center; font-size: 170px; letter-spacing: -4px; }
  .card--logo .brand__tagline { font-size: 30px; margin-top: 2px; }
  .card--logo .brand__web { color: var(--ink); font-size: 20px; letter-spacing: 7px; margin-top: 14px; }
</style>
</head>
<body>
<main class="sheet">

  <section class="card card--details">
    <svg class="card__swoosh" viewBox="0 0 700 427" preserveAspectRatio="none" aria-hidden="true">
      <path d="M0,178 C150,176 330,270 450,400 C320,300 160,220 0,212 Z" fill="var(--yellow)"/>
      <path d="M0,218 C150,224 300,300 390,372 C270,318 130,290 0,292 Z" fill="var(--charcoal)"/>
      <path d="M0,350 C220,360 440,392 700,392 L700,427 L0,427 Z" fill="var(--yellow)"/>
    </svg>

    <div class="brand">
      <div class="brand__name">brisk<span class="brand__dot"></span></div>
      <div class="brand__tagline">forward insight</div>
    </div>

    <div class="divider"></div>

    <div class="contact">
      <div class="contact__name">Dana Pruitt <span>MRPC</span></div>
      <div class="contact__address">Level 4, 37 Quarrell St<br>Ashgrove Vale, NSW 2031</div>
      <div class="contact__row">
        <svg class="contact__icon" viewBox="0 0 16 16" aria-hidden="true"><circle cx="8" cy="8" r="8" fill="var(--yellow)"/><path d="M5 4.5h2l.6 2-1 .8a5 5 0 0 0 2.1 2.1l.8-1 2 .6v2c-4 .4-7-2.6-6.5-6.5z" fill="#fff"/></svg>
        <span>01 5550 1427</span>
      </div>
      <div class="contact__row">
        <svg class="contact__icon" viewBox="0 0 16 16" aria-hidden="true"><circle cx="8" cy="8" r="8" fill="var(--yellow)"/><rect x="5.5" y="3.5" width="5" height="9" rx="1" fill="#fff"/><rect x="6.5" y="4.7" width="3" height="5" fill="var(--yellow)"/></svg>
        <span>01 5550 8362</span>
      </div>
      <div class="contact__row">
        <svg class="contact__icon" viewBox="0 0 16 16" aria-hidden="true"><circle cx="8" cy="8" r="8" fill="var(--yellow)"/><rect x="3.5" y="5" width="9" height="6" fill="#fff"/><path d="M3.5 5l4.5 3.5L12.5 5" stroke="var(--yellow)" fill="none"/></svg>
        <span>dana@briskqr.com.au</span>
      </div>
      <div class="contact__row">
        <svg class="contact__icon" viewBox="0 0 16 16" aria-hidden="true"><circle cx="8" cy="8" r="8" fill="var(--yellow)"/><circle cx="8" cy="8" r="4.5" fill="none" stroke="#fff"/><ellipse cx="8" cy="8" rx="2" ry="4.5" fill="none" stroke="#fff"/><path d="M3.5 8h9" stroke="#fff"/></svg>
        <span>www.briskqr.com.au</span>
      </div>
    </div>
  </section>

  <section class="card card--logo">
    <div class="brand">
      <div class="brand__name">brisk</div>
      <div class="brand__tagline">forward insight</div>
      <div class="brand__web">www.briskqr.com.au</div>
    </div>
  </section>

</main>
</body>
</html>
```